Business Card Design

An energy company designed around renewable energy and energy storage that focuses on providing its energy at points on the grid that reduce costs and add value to the system.

Industry/Entity Type

Business

Contact Information for Business Card

Gavin Kellerby
Executive Vice President
53 K ST NE
Washington, DC 20019
301-555-0187
gkellerby@tallowmereco.com

```html
<!DOCTYPE html>
<html lang="en">
<head>
<meta charset="utf-8">
<title>Business Card – Gavin Kellerby</title>
<link href="https://fonts.googleapis.com/css2?family=Lato:wght@300;400;700;900&display=swap" rel="stylesheet">
<style>
  :root {
    --backdrop: #8f9597;
    --card-white: #f4f4f4;
    --card-dark: #252a2b;
    --brand-orange: #ff7a00;
    --ink-dark: #3a3d3f;
    --ink-white: #ffffff;
    --ink-soft: #ffe0c2;
    --divider: #d6d6d6;
  }
  * { box-sizing: border-box; margin: 0; padding: 0; }
  html, body { width: 1200px; height: 900px; overflow: hidden; }
  body {
    background: var(--backdrop);
    font-family: "Lato", Arial, sans-serif;
    position: relative;
  }
  .card {
    position: absolute;
    width: 600px;
    height: 343px;
    border-radius: 4px;
    overflow: hidden;
    box-shadow: 0 6px 18px rgba(0,0,0,0.25);
  }
  /* Back side */
  .card-back {
    left: 480px;
    top: 70px;
    background: var(--card-dark);
    display: flex;
    align-items: center;
    justify-content: center;
    gap: 18px;
  }
  .card-back .brand-square {
    width: 34px; height: 34px;
    background: var(--brand-orange);
  }
  .card-back .brand-name {
    color: var(--ink-white);
    font-weight: 900;
    font-size: 38px;
    letter-spacing: 3px;
    text-transform: uppercase;
  }
  /* Front side */
  .card-front {
    left: 120px;
    top: 440px;
    background: var(--card-white);
  }
  .front-header {
    height: 172px;
    display: flex;
    align-items: center;
    justify-content: center;
    gap: 16px;
    background: linear-gradient(#ffffff, #ececec);
  }
  .front-header .brand-square {
    width: 28px; height: 28px;
    background: var(--brand-orange);
  }
  .front-header .divider {
    width: 1px; height: 80px;
    background: var(--divider);
  }
  .front-header .brand-name {
    color: var(--ink-dark);
    font-weight: 900;
    font-size: 32px;
    letter-spacing: 3px;
    text-transform: uppercase;
  }
  .front-details {
    height: 171px;
    background: var(--brand-orange);
    display: flex;
    padding: 18px 0 0 0;
  }
  .person {
    width: 290px;
    padding-right: 22px;
    text-align: right;
    color: var(--ink-white);
  }
  .person-name { font-weight: 700; font-size: 22px; line-height: 1.15; }
  .person-title { font-weight: 400; font-size: 15px; color: var(--ink-soft); margin-bottom: 6px; }
  .person-address { font-size: 16px; line-height: 1.35; }
  .contacts {
    list-style: none;
    color: var(--ink-white);
    font-size: 17px;
    line-height: 1.45;
    padding-left: 6px;
  }
  .contacts li { display: flex; align-items: center; gap: 7px; white-space: nowrap; }
  .contact-icon {
    width: 16px; height: 16px;
    background: var(--ink-white);
    border-radius: 3px;
    flex: none;
  }
</style>
</head>
<body>

  <section class="card card-back" aria-label="Card back">
    <span class="brand-square"></span>
    <span class="brand-name">Gavin Kellerby</span>
  </section>

  <section class="card card-front" aria-label="Card front">
    <header class="front-header">
      <span class="brand-square"></span>
      <span class="divider"></span>
      <span class="brand-name">Gavin Kellerby</span>
    </header>
    <div class="front-details">
      <div class="person">
        <p class="person-name">Gavin Kellerby</p>
        <p class="person-title">Executive Vice President</p>
        <p class="person-address">53 K ST NE<br>Washington, DC 20019</p>
      </div>
      <ul class="contacts">
        <li>
          <svg class="contact-icon" viewBox="0 0 16 16" aria-hidden="true"><path d="M4 4c1-1 2 0 2 1l-1 1c1 2 2 3 4 4l1-1c1 0 2 1 1 2-1 1-2 1-4 0-2-1-3-2-4-4-1-2 0-3 1-3z" fill="#ff7a00"/></svg>
          <span>301-555-0187</span>
        </li>
        <li>
          <svg class="contact-icon" viewBox="0 0 16 16" aria-hidden="true"><path d="M6 10l4-4M5 8l-1 1a2 2 0 003 3l1-1M11 8l1-1a2 2 0 00-3-3L8 5" stroke="#ff7a00" stroke-width="1.5" fill="none"/></svg>
          <span>www.tallowmereco.com</span>
        </li>
        <li>
          <svg class="contact-icon" viewBox="0 0 16 16" aria-hidden="true"><rect x="3" y="4.5" width="10" height="7" fill="#ff7a00"/><path d="M3 4.5l5 4 5-4" stroke="#fff" fill="none"/></svg>
          <span>gkellerby@tallowmereco.com</span>
        </li>
      </ul>
    </div>
  </section>

</body>
</html>
```